E-Book-Cover für Ratgeber zum Thema Weisheit
Zielgruppe
Ich bin ein experimenteller Schriftsteller, der ein E-Book über Quellbuch Verlagsdienst auf Buchora veröffentlichen möchte. Das Thema des Ratgebers ist Weisheit.
Weisheit gilt als ein eher antiquierter und abstrakter Begriff. Das ist ein Irrtum. Sie ist wichtiger als je zuvor und kann beschrieben werden. Weder ist sie gleichzusetzen mit Klugheit, noch mit spiritueller Erleuchtung. Sie beinhaltet bestimmte Eigenschaften wie Vernunft, Wissbegierde, Demut, Einfühlungsvermögen, Intuition, Auflehnung... Wobei rationales Denken das oberste Gebot ist. Es wird u.a. gezeigt, was Weisheit für das eigene Leben bringt und wie man sie anstreben kann.
Die Zielgruppe sind alle Menschen, die an Philosophie, Psychologie, Selbstoptimierung oder Religionen bzw. Atheismus interessiert sind. Menschen, die nach einer Erkenntnis oder 'Erleuchtung' suchen und etwas Besonderes in der Bücherflut entdecken möchten. Es ist weniger für Akademiker geschrieben; eher für die 'normale', durchschnittliche Bevölkerung und kann auch von bildungsferneren Schichten aller Altersgruppen verstanden werden.
Meine Vermutung ist, dass es bei offenen Personen mittleren Alters Anklang finden könnte.
Aufgabenstellung
Der Titel und der Untertitel des Buches müssen vorkommen (Titel: 'Der Klare Blick'; Untertitel: 'Wie Sie mit dem revolutionären Konzept der modernen Weisheit wahre Größe erlangen'). Außerdem soll ein runder Button/Aufkleber/Sticker auf dem Cover kleben, welcher folgenden Text enthält: 'Mit Selbsttest! Wie weise bin ich?').
Natürlich soll der Name des Autors ebenfalls vorkommen: 'Malte Ruhland'
Das Cover soll sehr aus der Masse herausstechen, demnach ein echter Hingucker sein. Der potenzielle Kunde soll sofort neugierig sein! Es muss sowohl klein (als Thumbnail und am Smartphone), als auch groß gut aussehen und der Titel stets gut lesbar sein. Außerdem muss es schwarzweiß gut aussehen und erkennbar sein (für ebook-reader).
Buchora gibt folgende Werte für die Bilddatei vor: Die idealen Abmessungen für Coverdateien liegen bei 2 560 x 1 600 Pixeln. Mindestens 300 dpi. Die Größe der Bilddatei sollte 50MB nicht übersteigen. Farbprofil: RGB. DATEIFORMAT: JPG oder TIFF
Coverbilder mit weißem oder sehr hellem Hintergrund heben sich kaum vom Hintergrund ab. Fügen Sie einen dünnen Rahmen (3–4 Pixel) in Mittelgrau hinzu, um die Ränder des Coverbilds besser sichtbar zu machen.
Welches Cover gut zum Thema Weisheit passt, überlasse ich Ihrer Genialität. Ich dachte vielleicht an eine Art Blitz, Supernova, Erleuchtung, Explosion, geometrische Form o.ä. Aber Sie können sich etwas ganz eigenes ausdenken. Es sollte eher abstrakt sein. Außerdem muss es klar, edel und modern wirken, weniger comichaft oder verspielt/kitschig. Es darf etwas aggressiv bzw. 'revolutionär' wirken.

```html
<!DOCTYPE html>
<html lang="de">
<head>
<meta charset="utf-8">
<title>Der Klare Blick – Malte Ruhland</title>
<link rel="stylesheet" href="https://fonts.googleapis.com/css2?family=Audiowide&family=Open+Sans:ital,wght@0,600;0,700;1,700&display=swap">
<style>
  :root {
    --sky: #6aaed6;
    --sky-deep: #3f8fc0;
    --sky-light: #a9d0ea;
    --mist: #e9edf5;
    --ink: #2a2935;
    --white: #ffffff;
    --sticker: #3a8fbf;
  }
  * { margin: 0; padding: 0; box-sizing: border-box; }
  html, body { width: 750px; height: 1200px; overflow: hidden; background: var(--white); }
  .cover {
    position: relative;
    width: 750px;
    height: 1200px;
    overflow: hidden;
    background: linear-gradient(180deg, #6aadd5 0%, #69acd4 30%, #7ab6dc 55%, var(--sky-deep) 85%);
  }
  .cover-art {
    position: absolute;
    left: 0; top: 330px;
    width: 750px; height: 760px;
    background:
      radial-gradient(ellipse 260px 330px at 360px 420px, rgba(255,255,255,0.95) 0%, rgba(240,244,250,0.9) 60%, rgba(240,244,250,0) 100%),
      radial-gradient(ellipse 220px 160px at 600px 160px, rgba(200,225,242,0.8) 0%, rgba(200,225,242,0) 100%),
      linear-gradient(180deg, rgba(122,182,220,0) 0%, rgba(63,143,192,0.6) 100%);
  }
  .ground {
    position: absolute;
    left: 0; bottom: 0;
    width: 750px; height: 230px;
  }
  .author {
    position: absolute;
    top: 38px; left: 0; width: 100%;
    text-align: center;
    font-family: "Audiowide", sans-serif;
    font-size: 34px;
    letter-spacing: 2px;
    color: var(--white);
    text-transform: uppercase;
  }
  .title {
    position: absolute;
    top: 92px; left: 0; width: 100%;
    text-align: center;
    font-family: "Audiowide", sans-serif;
    font-weight: 400;
    color: var(--white);
    text-transform: lowercase;
    line-height: 0.98;
  }
  .title-line { display: block; }
  .title-line--first { font-size: 118px; }
  .title-line--second { font-size: 146px; }
  .sticker {
    position: absolute;
    left: 24px; top: 370px;
    width: 164px; height: 164px;
    border-radius: 50%;
    background: var(--sticker);
    color: var(--white);
    font-family: "Open Sans", sans-serif;
    display: flex;
    flex-direction: column;
    align-items: center;
    justify-content: center;
    text-align: center;
    transform: rotate(-8deg);
    line-height: 1.15;
  }
  .sticker-label { font-weight: 600; font-size: 19px; }
  .sticker-question { font-weight: 700; font-style: italic; font-size: 26px; margin-top: 2px; }
  .subtitle {
    position: absolute;
    left: 0; top: 1058px; width: 100%;
    text-align: center;
    font-family: "Open Sans", sans-serif;
    font-weight: 700;
    font-size: 30px;
    line-height: 42px;
    color: var(--ink);
  }
  .subtitle em { font-style: italic; }
</style>
</head>
<body>
  <main class="cover">
    <div class="cover-art" role="img" aria-label="Illustration: weißer Kopf im Profil, ein Mann im Anzug steigt auf einer Leiter zu einer offenen Tür im Kopf, weiße Vögel fliegen davon, aufsteigende Pfeile vor blauen Wolken"></div>

    <svg class="ground" viewBox="0 0 750 230" aria-hidden="true">
      <path d="M0 20 Q 375 -10 750 30 L750 230 L0 230 Z" fill="var(--mist)"/>
    </svg>

    <p class="author">Malte Ruhland</p>

    <h1 class="title">
      <span class="title-line title-line--first">der klare</span>
      <span class="title-line title-line--second">blick</span>
    </h1>

    <div class="sticker">
      <span class="sticker-label">Mit<br>Selbsttest!</span>
      <span class="sticker-question">“Wie weise<br>bin ich?”</span>
    </div>

    <p class="subtitle">
      Wie Sie mit dem <em>revolutionären Konzept</em><br>
      der <em>modernen Weisheit</em><br>
      wahre Größe erlangen
    </p>
  </main>
</body>
</html>
```